you will use Ai to Copy the website Brivanta.com to come up with the basic frame work and it will give you the understanding of how I would like Kelbrava.com to be like. Kelbrava.com is a peer to peer rv rental site very similar to both of the other rv rental sites the difference is that are commission based 20% and above per rental and we will be one flat monthly rate and they keep all the earnings. Below is photo that will help you with the color scheme and the look and feel of the design

1 page

```html
<!DOCTYPE html>
<html lang="en">
<head>
<meta charset="utf-8">
<title>Kelbrava.com — Home Page</title>
<link href="https://fonts.googleapis.com/css2?family=Fraunces:ital,opsz,wght@0,9..144,500;0,9..144,600;1,9..144,600&family=DM+Sans:wght@400;500;600;700&family=JetBrains+Mono:wght@500;600&display=swap" rel="stylesheet">
<style>
:root{
  --board:#f0eee7;
  --cream:#f7f5ee;
  --cream-2:#f1efe5;
  --navy:#0f1a33;
  --navy-2:#16223f;
  --lime:#a4d233;
  --lime-dark:#7ea51c;
  --ink:#1b2230;
  --muted:#5d6472;
  --line:#e3e0d6;
  --orange:#f2a57a;
  --orange-text:#e0803f;
  --slate:#4d5766;
  --white:#ffffff;
}
*{box-sizing:border-box;margin:0;padding:0}
html,body{width:1200px;height:1200px;overflow:hidden;background:var(--board)}
body{font-family:"DM Sans",sans-serif;color:var(--ink)}
.board{position:absolute;left:0;top:0;width:1932px;height:1932px;transform:scale(.62112);transform-origin:0 0;background:var(--board)}
.board-title{position:absolute;left:237px;top:34px;font-size:22px;color:#8a8a86;font-weight:400;letter-spacing:.3px}
.abs{position:absolute}
.serif{font-family:"Fraunces",serif;font-weight:600;letter-spacing:-.2px}
.mono{font-family:"JetBrains Mono",monospace}
.eyebrow{font-size:7.5px;letter-spacing:2.2px;font-weight:600;color:var(--lime-dark);text-transform:uppercase}
.on-dark .eyebrow{color:var(--lime)}
.btn{display:inline-flex;align-items:center;justify-content:center;gap:5px;background:var(--lime);color:var(--navy);font-weight:600;border-radius:4px}

.page-left{position:absolute;left:237px;top:72px;width:703px;height:1860px;background:var(--cream);overflow:hidden}
.page-right{position:absolute;left:1018px;top:0;width:702px;height:1848px;background:var(--cream);overflow:hidden}

.hero{position:absolute;left:0;top:0;width:703px;height:501px;background:linear-gradient(180deg,#26303a 0%,#3a4a3e 30%,#2b3d2a 55%,#1d2a22 100%)}
.hero-glow{position:absolute;left:380px;top:150px;width:330px;height:260px;background:radial-gradient(ellipse at 60% 40%,rgba(214,168,110,.35),transparent 70%)}
.hero-shade{position:absolute;inset:0;background:linear-gradient(90deg,rgba(12,20,30,.55),rgba(12,20,30,.1) 70%)}
.nav{position:absolute;left:40px;right:39px;top:12px;height:20px;display:flex;align-items:center;color:#fff}
.logo{font-family:"Fraunces",serif;font-weight:600;font-size:19px;display:flex;align-items:center;gap:6px}
.nav-links{display:flex;gap:17px;font-size:7px;margin-left:118px}
.nav-login{margin-left:auto;font-size:7px;margin-right:7px}
.nav .btn{font-size:7px;height:19px;padding:0 11px}
.hero-tabs{position:absolute;left:120px;top:120px;display:flex;background:rgba(255,255,255,.14);border-radius:12px;padding:2px;font-size:7px;color:#fff}
.hero-tabs span{padding:6px 13px;border-radius:10px}
.hero-tabs .active{background:var(--lime);color:var(--navy);font-weight:600}
.hero h1{position:absolute;left:119px;top:154px;font-size:40px;line-height:38px;color:#fff}
.hero h1 em{color:var(--lime);font-style:italic}
.hero-sub{position:absolute;left:119px;top:244px;width:310px;font-size:8.6px;line-height:15.5px;color:#e4e6e2}
.search{position:absolute;left:40px;top:329px;width:623px;height:116px;background:rgba(20,30,40,.45);border:1px solid rgba(255,255,255,.12);border-radius:6px;padding:8px}
.field-row{display:flex;gap:6px;margin-bottom:6px}
.field{flex:1;height:31px;background:#eef0ee;border-radius:3px;padding:5px 10px 0 24px;position:relative}
.field .ic{position:absolute;left:9px;top:11px;width:8px;height:8px;border:1px solid #9aa0a0;border-radius:2px}
.field label{display:block;font-size:5.5px;letter-spacing:.8px;color:#666c70;font-weight:600}
.field div{font-size:7px;color:#222;margin-top:2px}
.field div.ph{color:#a5aaad}
.field .chev{position:absolute;right:9px;top:12px;width:5px;height:5px;border-right:1px solid #555;border-bottom:1px solid #555;transform:rotate(45deg)}
.search .btn{width:100%;height:24px;font-size:8px}
.trust{position:absolute;left:40px;top:458px;display:flex;gap:16px;font-size:7px;color:#dfe3df}
.trust span::before{content:"";display:inline-block;width:6px;height:6px;border:1px solid var(--lime);border-radius:50%;margin-right:6px;vertical-align:-1px}
.scroll-cue{position:absolute;left:349px;top:482px;color:#cfd3d0;font-size:10px}

.fleet{position:absolute;left:40px;top:560px;width:623px}
.fleet h2{font-size:26px;line-height:26px;margin-top:8px}
.fleet .lead{font-size:8.6px;line-height:15.5px;color:var(--muted);margin-top:10px;width:360px}
.view-all{position:absolute;right:0;top:98px;font-size:7px;font-weight:600}
.filters{display:flex;gap:7px;margin-top:17px}
.filters span{font-size:7px;padding:5px 9px;border:1px solid var(--line);border-radius:10px;background:#fff}
.filters .on{background:var(--lime);border-color:var(--lime);font-weight:600}
.cards{position:absolute;left:0;top:161px;display:grid;grid-template-columns:repeat(3,196px);column-gap:17.5px;row-gap:18px}
.card{height:258px;background:#fff;border:1px solid var(--line);border-radius:5px;overflow:hidden;position:relative}
.card .photo{height:146px}
.badges{position:absolute;left:8px;top:8px;display:flex;gap:3px}
.badges span{font-size:5.5px;padding:2px 5px;border-radius:7px;color:#fff;background:rgba(15,26,51,.8)}
.badges .ib{background:var(--lime);color:var(--navy);font-weight:600}
.fav{position:absolute;right:7px;top:7px;width:16px;height:16px;border-radius:50%;background:#fff;display:flex;align-items:center;justify-content:center}
.card-body{padding:10px 10px 0}
.meta{display:flex;justify-content:space-between;font-size:5.6px;letter-spacing:.5px;color:var(--lime-dark);font-weight:600;margin-top:2px}
.meta b{color:var(--ink);font-weight:500;letter-spacing:0}
.meta b i{color:var(--orange-text);font-style:normal}
.card h3{font-family:"Fraunces",serif;font-weight:600;font-size:9.4px;margin-top:6px}
.card .loc,.card .sleeps{font-size:6.4px;color:var(--muted);margin-top:4px}
.card hr{border:0;border-top:1px solid var(--line);margin:7px 0 8px}
.price{display:flex;justify-content:space-between;align-items:flex-end}
.price strong{font-size:12px;font-weight:600}
.price strong small{font-size:6px;color:var(--muted);font-weight:400}
.price .vd{font-size:6.5px;font-weight:600}
.card .tp{font-size:5px;color:var(--muted);margin-top:3px}

.how{position:absolute;left:0;top:1313px;width:703px;height:365px;background:var(--navy);color:#fff;padding:60px 40px 0}
.how h2{font-size:26px;line-height:26px;margin-top:8px}
.steps{display:flex;gap:0;margin-top:26px}
.step{width:216px;padding-right:16px}
.step-top{display:flex;align-items:center;gap:10px}
.step-ic{width:28px;height:28px;border:1px solid rgba(164,210,51,.45);border-radius:4px;background:rgba(164,210,51,.12)}
.step-num{font-family:"JetBrains Mono",monospace;font-size:24px;color:#3b4763}
.step h4{font-family:"Fraunces",serif;font-weight:600;font-size:12px;margin-top:13px}
.step p{font-size:7px;line-height:13.5px;color:#b7bdca;margin-top:8px}
.how-links{position:absolute;left:40px;right:40px;top:279px;border-top:1px solid rgba(255,255,255,.1);padding-top:18px;font-size:6.5px;color:#9ea6b6;display:flex;gap:13px}
.how-links a{color:var(--lime);text-decoration:none}

.calc-peek{position:absolute;left:40px;top:1737px}
.calc-peek h2{font-size:24px;margin-top:8px}
.calc-peek p{font-size:8.6px;line-height:15.5px;color:var(--muted);margin-top:6px;width:310px}
.peek-card{position:absolute;top:1840px;width:300px;height:40px;background:#fff;border:1px solid var(--line);border-radius:5px}

.top-band{position:absolute;left:0;top:0;width:702px;height:54px;background:var(--navy)}
.calc{position:absolute;left:39px;top:115px;width:624px}
.calc h2{font-size:24px;margin-top:7px}
.calc .lead{font-size:8.6px;line-height:15.5px;color:var(--muted);margin-top:6px;width:310px}
.panel{position:absolute;top:101px;width:300px;height:283px;background:#fff;border:1px solid var(--line);border-radius:6px}
.income{left:0;padding:18px 19px}
.income .lbl{font-size:6.5px;letter-spacing:.5px;font-weight:600;color:#444}
.income .amount{font-size:19px;margin-top:6px;font-weight:600}
.income .amount small{font-family:"DM Sans",sans-serif;font-size:7px;color:var(--muted);font-weight:400}
.slider{position:relative;height:3px;background:#222;border-radius:2px;margin-top:9px}
.slider .fill{position:absolute;left:0;top:0;height:3px;width:71px;background:var(--lime);border-radius:2px}
.slider .knob{position:absolute;left:67px;top:-3px;width:9px;height:9px;border-radius:50%;background:var(--lime);border:1px solid #fff}
.range{display:flex;justify-content:space-between;font-size:5.8px;color:var(--muted);margin-top:7px}
.exact{display:flex;align-items:center;gap:6px;font-size:6.5px;color:#444;margin-top:8px}
.exact span{border:1px solid var(--line);border-radius:3px;width:72px;height:18px;padding:4px 6px;font-family:"JetBrains Mono",monospace;color:#222}
.row{display:flex;justify-content:space-between;font-size:7px;color:#333}
.row .neg{font-family:"JetBrains Mono",monospace;color:var(--orange-text)}
.keep{border-top:1px solid var(--line);margin-top:12px;padding-top:10px}
.keep .big{font-family:"JetBrains Mono",monospace;color:var(--lime-dark);font-size:12px;font-weight:600}
.keep .pos{font-family:"JetBrains Mono",monospace;color:var(--lime-dark)}
.income .btn{width:100%;height:27px;font-size:7.5px;margin-top:15px}
.chart{left:325px;padding:20px 19px}
.chart h4{font-family:"Fraunces",serif;font-weight:600;font-size:9.5px}
.chart .sub{font-size:6px;color:var(--muted);margin-top:4px}
.legend{display:flex;gap:14px;font-size:6.5px;color:#333;position:absolute;left:19px;top:214px}
.legend i{display:inline-block;width:6px;height:6px;border-radius:50%;margin-right:5px;vertical-align:0}
.note{position:absolute;left:19px;top:235px;width:262px;font-size:5.3px;line-height:10px;color:var(--muted)}

.list-photo{position:absolute;left:39px;top:686px;width:296px;height:250px;border-radius:6px;background:linear-gradient(160deg,#3a2416 0%,#7a4a26 35%,#b8793f 55%,#d9a15e 68%,#5a3520 100%);box-shadow:0 8px 18px rgba(0,0,0,.2)}
.rate-badge{position:absolute;left:1288px;top:676px;width:66px;height:66px;border-radius:50%;border:1px dashed #bfbcb0;background:var(--cream);display:flex;align-items:center;justify-content:center}
.rate-badge div{width:40px;height:40px;border-radius:50%;background:var(--lime);display:flex;flex-direction:column;align-items:center;justify-content:center;color:var(--navy);font-weight:700;font-size:11px;line-height:10px}
.rate-badge small{font-size:5px;font-weight:500}
.list-copy{position:absolute;left:368px;top:618px;width:300px}
.list-copy h2{font-size:26px;line-height:25px;margin-top:9px;width:235px}
.list-copy .lead{font-size:8.4px;line-height:15.3px;color:var(--muted);margin-top:13px}
.checks{list-style:none;margin-top:13px}
.checks li{font-size:7px;line-height:13px;padding-left:19px;position:relative;margin-bottom:7px}
.checks li::before{content:"";position:absolute;left:0;top:1px;width:10px;height:10px;border-radius:50%;background:rgba(164,210,51,.25)}
.checks li::after{content:"";position:absolute;left:3.5px;top:3px;width:2.5px;height:4.5px;border-right:1px solid var(--lime-dark);border-bottom:1px solid var(--lime-dark);transform:rotate(45deg)}
.list-actions{display:flex;align-items:center;gap:10px;margin-top:10px;font-size:6.5px;font-weight:600}
.list-actions .btn{height:26px;padding:0 15px;font-size:7px}
.list-copy .fine{font-size:5.8px;line-height:12px;color:var(--muted);margin-top:13px}

.why{position:absolute;left:0;top:1068px;width:702px;height:430px;background:var(--cream-2);padding:59px 39px 0}
.why h2{font-size:26px;line-height:26px;margin-top:9px}
.why .lead{font-size:8.6px;line-height:15.5px;color:var(--muted);margin-top:12px;width:360px}
.features{display:grid;grid-template-columns:repeat(3,196px);column-gap:18px;margin-top:24px}
.feature{height:149px;background:#fff;border:1px solid var(--line);border-radius:5px;padding:16px 16px}
.feature .ic{width:30px;height:30px;border-radius:5px;background:rgba(164,210,51,.18)}
.feature h4{font-family:"Fraunces",serif;font-weight:600;font-size:10px;line-height:15px;margin-top:14px}
.feature p{font-size:6.8px;line-height:13.5px;color:var(--muted);margin-top:6px}
.why-links{display:flex;gap:14px;font-size:7px;font-weight:600;margin-top:22px}

.footer{position:absolute;left:0;top:1498px;width:702px;height:350px;background:var(--navy);color:#fff;overflow:hidden}
.footer-rings{position:absolute;left:300px;top:60px;width:340px;height:340px;border-radius:50%;border:1px solid rgba(255,255,255,.04);box-shadow:0 0 0 40px rgba(255,255,255,.015)}
.footer h2{position:absolute;left:39px;top:42px;font-size:25px;line-height:26px}
.footer .lead{position:absolute;left:39px;top:100px;width:230px;font-size:7px;line-height:13px;color:#aab1c0}
.subscribe{position:absolute;left:364px;top:56px;width:300px}
.subscribe label{font-size:6.5px;color:#d6dae2}
.sub-row{display:flex;gap:6px;margin-top:5px}
.sub-row span{flex:1;height:24px;border:1px solid rgba(255,255,255,.15);border-radius:3px;background:rgba(255,255,255,.04);font-size:6.5px;color:#8791a5;padding:7px 8px}
.sub-row .btn{width:75px;height:24px;font-size:7px}
.consent{font-size:5px;color:#8f98aa;margin-top:8px;display:flex;align-items:center;gap:5px}
.consent i{width:6px;height:6px;background:#fff;border-radius:1px}
.f-brand{position:absolute;left:39px;top:183px}
.f-brand .logo{font-size:19px}
.f-tag{font-size:5.5px;letter-spacing:2px;color:var(--lime);margin-top:7px}
.f-desc{font-size:6.2px;line-height:12px;color:#9aa3b4;margin-top:13px;width:160px}
.f-trust{font-size:6.5px;color:#c9cfdb;margin-top:12px}
.f-col{position:absolute;top:185px}
.f-col h5{font-size:6.5px;letter-spacing:.6px;font-weight:700}
.f-col a{display:block;font-size:6.2px;color:#9aa3b4;text-decoration:none;margin-top:11.5px}
.f-bottom{position:absolute;left:39px;right:39px;top:312px;border-top:1px solid rgba(255,255,255,.08);padding-top:14px;display:flex;justify-content:space-between;font-size:6px;color:#8a93a6}
.f-bottom div{display:flex;gap:12px}
</style>
</head>
<body>
<div class="board">
  <div class="board-title">01 Home Page</div>

  <div class="page-left">
    <section class="hero">
      <div class="hero-glow"></div>
      <div class="hero-shade" role="img" aria-label="Photo of a motorhome on a winding mountain road through pine forest at dusk"></div>
      <nav class="nav">
        <div class="logo">Kelbrava.com</div>
        <div class="nav-links"><span>Browse RVs</span><span>How it works</span><span>For owners</span><span>Help</span></div>
        <span class="nav-login">Log in</span>
        <span class="btn">☷ List your RV</span>
      </nav>
      <div class="hero-tabs"><span class="active">I want to Rent</span><span>I want to List</span></div>
      <h1 class="serif">The open road is<br><em>calling.</em> Answer it.</h1>
      <p class="hero-sub">Rent handpicked RVs from real owners across the country. Honest prices, no middleman markups — just you, the keys, and the horizon.</p>
      <div class="search">
        <div class="field-row">
          <div class="field"><i class="ic"></i><label>WHERE</label><div class="ph">City, park, or ZIP</div></div>
          <div class="field"><i class="ic"></i><label>PICKUP DATE</label><div>mm/dd/yyyy</div></div>
          <div class="field"><i class="ic"></i><label>RETURN DATE</label><div>mm/dd/yyyy</div></div>
          <div class="field"><i class="ic"></i><label>GUESTS</label><div>2 guests</div><i class="chev"></i></div>
        </div>
        <div class="field-row">
          <div class="field"><i class="ic"></i><label>RENTAL MODE</label><div>I'll pick it up</div><i class="chev"></i></div>
          <div class="field"><i class="ic"></i><label>RV TYPE (OPTIONAL)</label><div>Any type</div><i class="chev"></i></div>
        </div>
        <span class="btn">
          <svg width="8" height="8" viewBox="0 0 10 10"><circle cx="4" cy="4" r="3" fill="none" stroke="#0f1a33" stroke-width="1.3"/><path d="M6.3 6.3 9 9" stroke="#0f1a33" stroke-width="1.3"/></svg>
          Search RVs</span>
      </div>
      <div class="trust"><span>Verified owners</span><span>Transparent pricing</span><span>Insurance protection</span><span>24/7 roadside support</span></div>
      <div class="scroll-cue">↓</div>
    </section>

    <section class="fleet">
      <div class="eyebrow">The Fleet</div>
      <h2 class="serif">Handpicked RVs,<br>ready when you are</h2>
      <p class="lead">Every rig is owner-maintained and road-ready. Honest rates from real people — no commission baked into the price.</p>
      <span class="view-all">View all RVs ›</span>
      <div class="filters"><span class="on">All</span><span>Class A</span><span>Class B</span><span>Class C</span><span>Travel Trailer</span><span>Fifth Wheel</span><span>Teardrop</span></div>

      <div class="cards">
        <article class="card">
          <div class="photo" role="img" aria-label="Class A motorhome on a canyon overlook at sunset" style="background:linear-gradient(180deg,#3b4a63 0%,#c98a52 40%,#7a4a2c 70%,#3a2a20 100%)"></div>
          <div class="badges"><span class="ib">⚡ Instant Book</span><span>Delivery</span></div>
          <div class="fav"><svg width="7" height="7" viewBox="0 0 10 9"><path d="M5 8.5 1 4.5A2.3 2.3 0 0 1 5 1.6 2.3 2.3 0 0 1 9 4.5Z" fill="none" stroke="#333"/></svg></div>
          <div class="card-body">
            <div class="meta">CLASS A <b><i>★</i> 4.9 (127)</b></div>
            <h3>Wanderlust Class A Diesel</h3>
            <div class="loc">⌖ Sedona, Arizona</div>
            <div class="sleeps">Sleeps 6 · Pet-friendly</div>
            <hr>
            <div class="price"><strong>$185 <small>/night</small></strong><span class="vd">View details →</span></div>
            <div class="tp">Transparent pricing</div>
          </div>
        </article>
        <article class="card">
          <div class="photo" role="img" aria-label="Camper van beside a mountain lake" style="background:linear-gradient(180deg,#b9c0c6 0%,#8d8f86 35%,#4f5b4a 65%,#2c3a34 100%)"></div>
          <div class="badges"><span class="ib">⚡ Instant Book</span><span>Delivery</span></div>
          <div class="fav"><svg width="7" height="7" viewBox="0 0 10 9"><path d="M5 8.5 1 4.5A2.3 2.3 0 0 1 5 1.6 2.3 2.3 0 0 1 9 4.5Z" fill="none" stroke="#333"/></svg></div>
          <div class="card-body">
            <div class="meta">CLASS B <b><i>★</i> 4.8 (89)</b></div>
            <h3>Nomad Van — Class B</h3>
            <div class="loc">⌖ Lake Tahoe, California</div>
            <div class="sleeps">Sleeps 2 · Pet-friendly</div>
            <hr>
            <div class="price"><strong>$145 <small>/night</small></strong><span class="vd">View details →</span></div>
            <div class="tp">Transparent pricing</div>
          </div>
        </article>
        <article class="card">
          <div class="photo" role="img" aria-label="Travel trailer camped in a pine forest" style="background:linear-gradient(180deg,#5d6a45 0%,#3f4c2e 45%,#6d5b3d 75%,#3b3020 100%)"></div>
          <div class="badges"><span>Delivery</span></div>
          <div class="fav"><svg width="7" height="7" viewBox="0 0 10 9"><path d="M5 8.5 1 4.5A2.3 2.3 0 0 1 5 1.6 2.3 2.3 0 0 1 9 4.5Z" fill="none" stroke="#333"/></svg></div>
          <div class="card-body">
            <div class="meta">TRAVEL TRAILER <b><i>★</i> 4.7 (64)</b></div>
            <h3>Pinecrest Travel Trailer</h3>
            <div class="loc">⌖ Bend, Oregon</div>
            <div class="sleeps">Sleeps 4 · Pet-friendly</div>
            <hr>
            <div class="price"><strong>$95 <small>/night</small></strong><span class="vd">View details →</span></div>
            <div class="tp">Transparent pricing</div>
          </div>
        </article>
        <article class="card">
          <div class="photo" role="img" aria-label="Fifth wheel trailer and truck in red desert canyon country" style="background:linear-gradient(180deg,#6d6f86 0%,#d59a74 35%,#a45a38 65%,#5a3324 100%)"></div>
          <div class="badges"><span class="ib">⚡ Instant Book</span><span>Delivery</span></div>
          <div class="fav"><svg width="7" height="7" viewBox="0 0 10 9"><path d="M5 8.5 1 4.5A2.3 2.3 0 0 1 5 1.6 2.3 2.3 0 0 1 9 4.5Z" fill="none" stroke="#333"/></svg></div>
          <div class="card-body">
            <div class="meta">FIFTH WHEEL <b><i>★</i> 4.9 (102)</b></div>
            <h3>Desert Rose Fifth Wheel</h3>
            <div class="loc">⌖ Moab, Utah</div>
            <div class="sleeps">Sleeps 5</div>
            <hr>
            <div class="price"><strong>$130 <small>/night</small></strong><span class="vd">View details →</span></div>
            <div class="tp">Transparent pricing</div>
          </div>
        </article>
        <article class="card">
          <div class="photo" role="img" aria-label="Class A motorhome on a canyon overlook at sunset" style="background:linear-gradient(180deg,#3b4a63 0%,#c98a52 40%,#7a4a2c 70%,#3a2a20 100%)"></div>
          <div class="badges"><span class="ib">⚡ Instant Book</span><span>Delivery</span></div>
          <div class="fav"><svg width="7" height="7" viewBox="0 0 10 9"><path d="M5 8.5 1 4.5A2.3 2.3 0 0 1 5 1.6 2.3 2.3 0 0 1 9 4.5Z" fill="none" stroke="#333"/></svg></div>
          <div class="card-body">
            <div class="meta">CLASS A <b><i>★</i> 4.9 (127)</b></div>
            <h3>Wanderlust Class A Diesel</h3>
            <div class="loc">⌖ Sedona, Arizona</div>
            <div class="sleeps">Sleeps 6 · Pet-friendly</div>
            <hr>
            <div class="price"><strong>$185 <small>/night</small></strong><span class="vd">View details →</span></div>
            <div class="tp">Transparent pricing</div>
          </div>
        </article>
        <article class="card">
          <div class="photo" role="img" aria-label="Camper van beside a mountain lake" style="background:linear-gradient(180deg,#b9c0c6 0%,#8d8f86 35%,#4f5b4a 65%,#2c3a34 100%)"></div>
          <div class="badges"><span class="ib">⚡ Instant Book</span><span>Delivery</span></div>
          <div class="fav"><svg width="7" height="7" viewBox="0 0 10 9"><path d="M5 8.5 1 4.5A2.3 2.3 0 0 1 5 1.6 2.3 2.3 0 0 1 9 4.5Z" fill="none" stroke="#333"/></svg></div>
          <div class="card-body">
            <div class="meta">CLASS B <b><i>★</i> 4.8 (89)</b></div>
            <h3>Nomad Van — Class B</h3>
            <div class="loc">⌖ Lake Tahoe, California</div>
            <div class="sleeps">Sleeps 2 · Pet-friendly</div>
            <hr>
            <div class="price"><strong>$145 <small>/night</small></strong><span class="vd">View details →</span></div>
            <div class="tp">Transparent pricing</div>
          </div>
        </article>
      </div>
    </section>

    <section class="how on-dark">
      <div class="eyebrow">How it works</div>
      <h2 class="serif">From driveway to<br>destination in three steps</h2>
      <div class="steps">
        <div class="step"><div class="step-top"><span class="step-ic"></span><span class="step-num">01</span></div><h4>Find your RV</h4><p>Search by location, dates, and rig type. Filter for instant book, delivery, and pet-friendly options.</p></div>
        <div class="step"><div class="step-top"><span class="step-ic"></span><span class="step-num">02</span></div><h4>Book securely</h4><p>Message the owner, confirm dates, and book with secure payments. Identity verification helps protect every trip.</p></div>
        <div class="step"><div class="step-top"><span class="step-ic"></span><span class="step-num">03</span></div><h4>Pick up or get delivery</h4><p>Pick up the keys and get a walkthrough, or have the RV delivered to your campsite. Then chase the horizon.</p></div>
      </div>
      <div class="how-links">Protected every mile: <a>Insurance →</a><a>Trust &amp; Safety →</a><a>Roadside Assistance →</a><a>Cancellation Policy →</a></div>
    </section>

    <section class="calc-peek">
      <div class="eyebrow">The Profit Calculator</div>
      <h2 class="serif">See exactly what you keep</h2>
      <p>Adjust your expected monthly rental income and watch the gap between commission-based platforms and Kelbrava's flat fee grow.</p>
    </section>
    <div class="peek-card" style="left:40px"></div>
    <div class="peek-card" style="left:365px"></div>
  </div>

  <div class="page-right">
    <div class="top-band"></div>

    <section class="calc">
      <div class="eyebrow">The Profit Calculator</div>
      <h2 class="serif">See exactly what you keep</h2>
      <p class="lead">Adjust your expected monthly rental income and watch the gap between commission-based platforms and Kelbrava's flat fee grow.</p>

      <div class="panel income">
        <div class="lbl">◎ MONTHLY RENTAL INCOME</div>
        <div class="amount mono">$3,000 <small>/mo</small></div>
        <div class="slider"><div class="fill"></div><div class="knob"></div></div>
        <div class="range mono"><span>$500</span><span>$10,000</span></div>
        <div class="exact">Enter exact amount: <span>$ 3000</span></div>
        <div class="row" style="margin-top:18px"><span>Competitor fee (20%)</span><span class="neg">-$600</span></div>
        <div class="row" style="margin-top:10px"><span>Kelbrava flat fee</span><span class="neg">-$49</span></div>
        <div class="keep">
          <div class="row"><span style="font-weight:600">↗ You keep more / month</span><span class="big">+$551</span></div>
          <div class="row" style="margin-top:6px;font-size:6.5px"><span>Additional retained / year</span><span class="pos">+$6,612</span></div>
        </div>
        <span class="btn">Start your flat-rate plan →</span>
      </div>

      <div class="panel chart">
        <h4>Monthly earnings comparison</h4>
        <div class="sub">What lands in your pocket each month</div>
        <svg class="abs" style="left:12px;top:58px" width="270" height="145" viewBox="0 0 270 145">
          <g font-family="DM Sans,sans-serif" font-size="5.5" fill="#6b7280">
            <text x="6" y="8">3,000</text><text x="4" y="39">$2,250</text><text x="4" y="70">$1,500</text><text x="8" y="101">$750</text><text x="13" y="132">$0</text>
          </g>
          <rect x="61" y="32" width="24" height="98" rx="2" fill="#4d5766"/>
          <rect x="88" y="105" width="24" height="25" rx="2" fill="#f2a57a"/>
          <rect x="179" y="8" width="24" height="122" rx="2" fill="#a4d233"/>
          <rect x="206" y="128" width="24" height="2" fill="#f2a57a"/>
          <line x1="30" y1="130.5" x2="265" y2="130.5" stroke="#e3e0d6"/>
          <g font-family="DM Sans,sans-serif" font-size="6" fill="#333" text-anchor="middle">
            <text x="87" y="141">Competitors</text><text x="205" y="141">Kelbrava</text>
          </g>
        </svg>
        <div class="legend"><span><i style="background:var(--lime)"></i>Your earnings</span><span><i style="background:var(--orange)"></i>Platform fees</span></div>
        <p class="note">Example based on a 20% commission-based platform fee. Actual competitor fees vary by platform and listing. Does not include applicable payment-processing or optional insurance costs.</p>
      </div>
    </section>

    <div class="list-photo" role="img" aria-label="Photo of a warm wood-panelled RV interior with leather seats and a table by the window at sunset"></div>

    <section class="list-copy">
      <div class="eyebrow">List your RV</div>
      <h2 class="serif">Stop splitting your earnings. Start banking them.</h2>
      <p class="lead">Other platforms skim 20% or more off every booking. We took a different road: create your listing for free, then activate your $49/month flat-rate plan when you're ready to accept bookings.</p>
      <ul class="checks">
        <li>Create your listing for free — no upfront cost</li>
        <li>Activate the $49/month flat-rate plan when you're ready to accept bookings</li>
        <li>Set your own nightly rate, minimums, and availability calendar</li>
        <li>Unlimited listing photos, messaging, and reviews included</li>
        <li>Secure payment workflow with payouts to your account</li>
        <li>Renter identity verification and listing protection options</li>
      </ul>
      <div class="list-actions"><span class="btn">Start your free listing →</span><span>View flat-fee pricing</span><span>See owner protection</span></div>
      <p class="fine">The $49/month plan begins when you activate it to accept bookings. You can pause or cancel anytime. Payment-processing and optional insurance costs may apply; taxes may apply depending on your location. Owners receive payouts for completed trips through the secure payment workflow.</p>
    </section>

    <section class="why">
      <div class="eyebrow">Why Kelbrava</div>
      <h2 class="serif">A marketplace built<br>on fair, honest pricing</h2>
      <p class="lead">We replaced per-booking commission with one transparent flat fee — so renters pay less and owners keep more of every trip.</p>
      <div class="features">
        <div class="feature"><div class="ic"></div><h4>Transparent, flat-fee pricing</h4><p>Renters see honest nightly rates with no commission baked in. Owners pay one flat monthly fee and keep what they earn — no per-booking surprises.</p></div>
        <div class="feature"><div class="ic"></div><h4>Verified owners &amp; secure payments</h4><p>Owner identity verification and a secure payment workflow help protect every booking, on both sides of the keys.</p></div>
        <div class="feature"><div class="ic"></div><h4>Insurance &amp; 24/7 roadside help</h4><p>Insurance protection options and 24/7 roadside assistance are available so help is never far away, wherever the road takes you.</p></div>
      </div>
      <div class="why-links"><span>Read our Trust &amp; Safety promise →</span><span>Learn about listing your RV →</span></div>
    </section>

    <footer class="footer">
      <div class="footer-rings"></div>
      <h2 class="serif">Your next adventure<br>starts with one flat fee</h2>
      <p class="lead">Get renter deals and owner tips from Kelbrava. For both renters and owners.</p>
      <div class="subscribe">
        <label>Email address</label>
        <div class="sub-row"><span>✉ you@email.com</span><b class="btn">Subscribe →</b></div>
        <div class="consent"><i></i>I agree to receive marketing emails and accept the Privacy Policy. Unsubscribe anytime.</div>
      </div>
      <div class="f-brand">
        <div class="logo">Kelbrava.com</div>
        <div class="f-tag">LIST IT · RENT IT · BANK IT</div>
        <p class="f-desc">The peer-to-peer RV marketplace built on a flat fee. No commission, ever.</p>
        <div class="f-trust">◇ Trust &amp; Safety</div>
      </div>
      <div class="f-col" style="left:254px"><h5>RENT</h5><a>Browse RVs</a><a>How it works</a><a>Instant Book</a><a>Insurance</a><a>Roadside Assistance</a></div>
      <div class="f-col" style="left:361px"><h5>LIST</h5><a>List your RV</a><a>Flat-fee pricing</a><a>Owner resources</a><a>Profit calculator</a></div>
      <div class="f-col" style="left:469px"><h5>COMPANY</h5><a>About</a><a>Contact</a><a>Help Center</a><a>Trust &amp; Safety</a></div>
      <div class="f-col" style="left:577px"><h5>LEGAL</h5><a>Terms</a><a>Privacy</a><a>Cookies</a><a>Cancellation Policy</a></div>
      <div class="f-bottom"><span>© 2026 Kelbrava.com — Flat fee. Full freedom.</span><div><span>Terms</span><span>Privacy</span><span>Cookies</span></div></div>
    </footer>
  </div>

  <div class="rate-badge"><div>$49<small>/mo</small></div></div>
</div>
</body>
</html>
```